Interior Design/ decoration business card design

This card is for my Interior Design and Decoration business and later I will also be selling homewares. I would like the card to be very simple in design and like either white, duck egg blue , aquas or metallics on a flat mat card excellent quality card. It needs to be well designed as that is my field. I dont like fuss, the simpler the better. I would like a styalised brim under the name brim if possible. SIMPLE, STYLISH, CLASSIC, TASTEFUL

Target Market(s)

40 + year olds who are building or rennovating.

Industry/Entity Type

Business

Contact Information for Business Card

Brim
styling, design, homeware

Marnie Callow
p 0427163958
e marnie@brimhouse.com.au
w brimhouse.com.au

Requirements
Must have
• very simple, stylish, classic, sophisticated. Simple and easy to read text that is a print similar to attached image. I like simple round A's though not as in attached image.

Double sided. It wont save as double sided for some reason!!
Should not have
• not too much colour, No animated / cartoon pictures.

```html
<!DOCTYPE html>
<html lang="en">
<head>
<meta charset="utf-8">
<title>Brim business card</title>
<link href="https://fonts.googleapis.com/css2?family=Quicksand:wght@300&family=Oswald:wght@500&family=Exo+2:wght@400&display=swap" rel="stylesheet">
<style>
  :root {
    --backdrop: #d9d7d4;
    --paper: #ffffff;
    --charcoal: #353333;
    --umber: #4b3e35;
    --ink: #2f2b28;
    --mist: #e9e9e9;
  }
  html, body {
    margin: 0;
    width: 1200px;
    height: 892px;
    overflow: hidden;
    background: var(--backdrop);
  }
  .canvas {
    position: relative;
    width: 1200px;
    height: 892px;
  }
  .card {
    position: absolute;
    top: 291px;
    width: 540px;
    height: 309px;
    box-shadow: 0 10px 28px rgba(0,0,0,0.22);
    overflow: hidden;
    background: var(--paper);
  }
  .card--front { left: 40px; }
  .card--back { left: 620px; }
  .card svg.panels {
    position: absolute;
    inset: 0;
  }
  .wordmark {
    position: absolute;
    display: flex;
    align-items: center;
    gap: 12px;
    font-family: "Quicksand", sans-serif;
    font-weight: 300;
    color: var(--ink);
    line-height: 1;
  }
  .wordmark__dot {
    border-radius: 50%;
    border: 1.5px solid var(--ink);
  }
  .card--front .wordmark {
    left: 50%;
    top: 50%;
    transform: translate(-50%, -50%);
    font-size: 64px;
  }
  .card--front .wordmark__dot { width: 14px; height: 14px; }
  .card--back .wordmark {
    right: 40px;
    top: 28px;
    font-size: 40px;
  }
  .card--back .wordmark__dot { width: 10px; height: 10px; }
  .holder {
    position: absolute;
    left: 22px;
    top: 222px;
    color: var(--ink);
  }
  .holder__name {
    font-family: "Oswald", sans-serif;
    font-weight: 500;
    font-size: 24px;
    letter-spacing: 0.5px;
    line-height: 1;
  }
  .holder__role {
    font-family: "Exo 2", sans-serif;
    font-size: 10px;
    letter-spacing: 2px;
    margin-top: 6px;
  }
  .contacts {
    position: absolute;
    left: 252px;
    top: 152px;
    margin: 0;
    padding: 0;
    list-style: none;
    font-family: "Exo 2", sans-serif;
    font-size: 10.5px;
    line-height: 1.35;
    color: var(--mist);
  }
  .contacts__row {
    display: flex;
    align-items: center;
    gap: 12px;
    margin-bottom: 10px;
  }
  .contacts__icon {
    flex: none;
    width: 24px;
    height: 24px;
  }
</style>
</head>
<body>
<main class="canvas">

  <section class="card card--front" aria-label="Card front">
    <div class="wordmark"><span class="wordmark__name">brim</span><span class="wordmark__dot"></span></div>
  </section>

  <section class="card card--back" aria-label="Card back">
    <svg class="panels" width="540" height="309" viewBox="0 0 540 309" aria-hidden="true">
      <rect width="540" height="309" fill="var(--charcoal)"/>
      <polygon points="0,0 250,0 125,50 0,75" fill="var(--umber)"/>
      <polygon points="250,0 540,0 540,105 170,140" fill="var(--paper)"/>
      <polygon points="0,75 125,50 240,200 150,309 0,309" fill="var(--paper)"/>
      <polygon points="260,309 540,230 540,309" fill="var(--umber)"/>
    </svg>

    <div class="wordmark"><span class="wordmark__name">brim</span><span class="wordmark__dot"></span></div>

    <div class="holder">
      <div class="holder__name">MARNIE CALLOW</div>
      <div class="holder__role">GENERAL MANAGER</div>
    </div>

    <ul class="contacts">
      <li class="contacts__row">
        <svg class="contacts__icon" viewBox="0 0 24 24" aria-hidden="true">
          <circle cx="12" cy="12" r="12" fill="var(--paper)"/>
          <path d="M6 12.5 L12 7 L18 12.5 M8 11.5 V17 H16 V11.5" fill="none" stroke="var(--charcoal)" stroke-width="1.8"/>
        </svg>
        <span>14 Linden Lane,<br>Hawthorn East</span>
      </li>
      <li class="contacts__row">
        <svg class="contacts__icon" viewBox="0 0 24 24" aria-hidden="true">
          <circle cx="12" cy="12" r="12" fill="var(--paper)"/>
          <circle cx="12" cy="12" r="6" fill="none" stroke="var(--charcoal)" stroke-width="1.5"/>
          <path d="M6 12 H18 M12 6 C9 9 9 15 12 18 M12 6 C15 9 15 15 12 18" fill="none" stroke="var(--charcoal)" stroke-width="1.2"/>
        </svg>
        <span>p 0427163958<br>p 0427163958</span>
      </li>
      <li class="contacts__row">
        <svg class="contacts__icon" viewBox="0 0 24 24" aria-hidden="true">
          <circle cx="12" cy="12" r="12" fill="var(--paper)"/>
          <rect x="9" y="6" width="6" height="12" rx="1" fill="none" stroke="var(--charcoal)" stroke-width="1.5"/>
          <line x1="11" y1="15.8" x2="13" y2="15.8" stroke="var(--charcoal)" stroke-width="1.2"/>
        </svg>
        <span>marnie@brimhouse.com.au<br>www.brimhouse.com.au</span>
      </li>
    </ul>
  </section>

</main>
</body>
</html>
```